THE Harbourline Mobility Foundation (HMF) PHOTOGRAPHY COMPETITION

We need a "flyer" (must be web friendly" as well as A5 Print) designed that will announce the launch of a new photography competition. The Theme of the Competition will be "Life Goes On".

Harbourline Mobility Foundation will "host" a competition that is open to all comers, irrespective of experience, but within the following Classes : 1. People Living with Spinal Injuries 2. Schools 3. Amateur Under 18 Photographers 4. Amateur Over 18 Photographers 5. Charities 6. Professional Photographers.

The competition will start in October 2018 and entries will be accepted via the HMF website until 31st August 2019. Prizes to include a Cash Prize of £7,500 for the photograph that in the opinion of the judges best meets the brief. Each Class winner and runner up will receive photographic equipment (a camera for the winner, a tripod for the runner up). The two best photographs in each class will be included in HMF's 2020 Calendar. Prizes will be presented at an event in Salisbury in October 2019.

Entry Fee (payable via the HMF website) will be £2.00 per photograph.

Please note that this is an initial "draft" and any published "flyer / web page will have to meet current UK Charity Regulations.

Telephone +44 (0)1632 960418

www.hmfcharity-example.org.uk (new website to be launched prior to Competition starting)

find us on facebook & twitter

Registered charity No. 1098452

Target Market(s)

Photographers, Schools, Charities

Industry/Entity Type

Charity

Font styles to use
Sans Serif

Colors

Designer to choose colors to be used in the design.

Requirements
Must have
• The HMF Logo
Nice to have
• Less words, high graphic appeal
Should not have
• Any doom and gloom! - People Living with Spinal Injuries are not "sick" - they are "Living With" Spinal Injury - not dieing from it!

```html
<!DOCTYPE html>
<html lang="en">
<head>
<meta charset="utf-8">
<title>Life Goes On – Photography Competition</title>
<link href="https://fonts.googleapis.com/css2?family=Libre+Baskerville:wght@700&family=Parisienne&family=Open+Sans:wght@400;700&display=swap" rel="stylesheet">
<style>
:root{
  --ink:#7a7066;
  --ink-dark:#6a6057;
  --sky:#5bc4e0;
  --paper:#fdfdfd;
  --paper-shade:#eeeeee;
  --white:#ffffff;
}
*{box-sizing:border-box;margin:0;padding:0}
html,body{width:948px;height:1200px;overflow:hidden;background:#e6e6e6}
.flyer{position:relative;width:948px;height:1200px;background:linear-gradient(180deg,var(--paper) 0%,var(--paper) 60%,var(--paper-shade) 100%);font-family:"Open Sans",Arial,sans-serif;color:var(--ink);overflow:hidden}
.shapes{position:absolute;left:0;top:0}
.title{position:absolute;left:0;width:948px;top:22px;text-align:center;font-family:"Libre Baskerville",Georgia,serif;font-weight:700;font-size:43px;letter-spacing:.5px;color:var(--ink)}
.theme{position:absolute;left:0;width:948px;top:70px;text-align:center;font-family:"Parisienne",cursive;font-size:64px;color:var(--sky);line-height:1}
.brand{position:absolute;left:62px;top:708px;width:200px;font-size:22px;line-height:23px;text-transform:uppercase;letter-spacing:.5px;color:var(--ink)}
.intro{position:absolute;left:291px;top:706px;width:626px;font-size:17.5px;line-height:24.5px;text-align:justify}
.prizes-banner{position:absolute;left:0;top:843px;width:256px;height:43px;padding-left:47px;font-weight:700;font-size:27px;line-height:43px;color:var(--white)}
.prize-list{position:absolute;left:0;top:904px;list-style:none}
.prize{position:relative;padding-left:73px;font-size:20px;line-height:25px;margin-bottom:19px;width:520px}
.prize strong{color:var(--ink-dark)}
.prize svg{position:absolute;left:38px;top:0}
.classes-intro{position:absolute;left:494px;top:848px;width:423px;font-size:17.5px;line-height:25px;text-align:justify}
.class-list{position:absolute;left:502px;top:922px;list-style:none}
.class-item{position:relative;padding-left:17px;font-size:17.5px;line-height:26px;height:26.2px}
.class-item svg{position:absolute;left:0;top:8px}
.contact{position:absolute;left:170px;top:1110px;width:597px;height:40px;border-radius:10px;background:var(--sky);box-shadow:0 3px 6px rgba(0,0,0,.15);color:var(--white);font-size:19px;display:flex;align-items:center;padding-left:34px;gap:30px}
.contact span{display:flex;align-items:center;gap:10px}
.social{position:absolute;top:1109px;width:40px;height:40px;border-radius:50%;background:var(--ink)}
.social.one{left:820px}
.social.two{left:875px}
.legal{position:absolute;left:0;width:948px;top:1172px;text-align:center;font-size:10.5px;color:var(--ink)}
</style>
</head>
<body>
<main class="flyer">
  <svg class="shapes" width="948" height="1200" viewBox="0 0 948 1200">
    <defs>
      <linearGradient id="family-tones" x1="0" y1="0" x2="1" y2="1">
        <stop offset="0" stop-color="#8a8a3a"/>
        <stop offset=".45" stop-color="#6e5a48"/>
        <stop offset="1" stop-color="#3d4a2a"/>
      </linearGradient>
      <linearGradient id="path-tones" x1="0" y1="0" x2="1" y2="1">
        <stop offset="0" stop-color="#6f8f4a"/>
        <stop offset=".5" stop-color="#7a6a5c"/>
        <stop offset="1" stop-color="#4e6a36"/>
      </linearGradient>
    </defs>
    <line x1="110" y1="116" x2="256" y2="116" stroke="var(--sky)" stroke-width="2"/>
    <line x1="694" y1="116" x2="840" y2="116" stroke="var(--sky)" stroke-width="2"/>
    <path d="M479,180 C430,140 330,135 230,150 C110,170 30,250 28,350 C28,440 90,510 200,570 C300,625 420,665 479,698 C540,665 660,625 760,570 C870,510 930,440 928,350 C926,250 850,170 730,150 C630,135 530,140 479,180 Z" fill="none" stroke="var(--sky)" stroke-width="2"/>
    <path role="img" aria-label="Photo of a smiling family outdoors in a garden, a father in a wheelchair holding a young child beside a mother with a baby" d="M479,186 C430,148 330,143 230,158 C115,177 37,254 36,350 C36,436 96,503 204,563 C302,617 420,657 479,689 C538,657 656,617 756,563 C864,503 921,436 920,350 C918,254 844,177 730,158 C630,143 528,148 479,186 Z" fill="url(#family-tones)"/>
    <path d="M751,462 C725,440 680,440 640,448 C590,460 563,495 565,540 C568,590 620,630 680,660 C715,678 740,690 751,697 C762,690 790,678 822,660 C880,630 935,590 935,540 C935,495 905,460 860,448 C820,440 775,440 751,462 Z" fill="var(--white)" stroke="var(--sky)" stroke-width="2"/>
    <path role="img" aria-label="Photo of a man riding a hand-cycle wheelchair along a grassy country path" d="M751,470 C725,449 682,449 643,456 C597,467 572,499 574,540 C577,586 625,623 683,652 C716,669 740,681 751,688 C762,681 787,669 819,652 C876,623 926,586 926,540 C926,499 899,467 857,456 C818,449 775,449 751,470 Z" fill="url(#path-tones)"/>
    <path d="M0,843 H256 L248,864 L256,886 H0 Z" fill="var(--sky)"/>
  </svg>

  <h1 class="title">PHOTOGRAPHY COMPETITION</h1>
  <p class="theme">Life Goes On</p>

  <div class="brand">Harbourline<br>Mobility<br>Foundation</div>

  <p class="intro">The competition will start in October 2018 and entries will be accepted via the HMF website until 31st August 2019. Prizes will be presented at an event in Salisbury in October 2019. Entry Fee (payable via the HMF website) will be £2.00 per photograph.</p>

  <div class="prizes-banner">PRIZES</div>
  <ul class="prize-list">
    <li class="prize"><svg width="28" height="34" viewBox="0 0 28 34"><path d="M8,18 L3,32 L9,29 L12,34 L14,22 L16,34 L19,29 L25,32 L20,18 Z" fill="var(--sky)"/><circle cx="14" cy="12" r="11" fill="var(--sky)"/></svg><strong>£7,500</strong> Cash Prize</li>
    <li class="prize"><svg width="28" height="34" viewBox="0 0 28 34"><path d="M8,18 L3,32 L9,29 L12,34 L14,22 L16,34 L19,29 L25,32 L20,18 Z" fill="var(--sky)"/><circle cx="14" cy="12" r="11" fill="var(--sky)"/></svg><strong>Camera</strong> for Each Class winner</li>
    <li class="prize"><svg width="28" height="34" viewBox="0 0 28 34"><path d="M8,18 L3,32 L9,29 L12,34 L14,22 L16,34 L19,29 L25,32 L20,18 Z" fill="var(--sky)"/><circle cx="14" cy="12" r="11" fill="var(--sky)"/></svg><strong>Tripod</strong> for runner up</li>
    <li class="prize"><svg width="28" height="34" viewBox="0 0 28 34"><path d="M8,18 L3,32 L9,29 L12,34 L14,22 L16,34 L19,29 L25,32 L20,18 Z" fill="var(--sky)"/><circle cx="14" cy="12" r="11" fill="var(--sky)"/></svg><strong>HMF's 2020 Calendar</strong> for the two best photographs in each class.</li>
  </ul>

  <p class="classes-intro">Competition that is open to all comers, irrespective of experience, but within the following Classes:</p>
  <ul class="class-list">
    <li class="class-item"><svg width="12" height="12" viewBox="0 0 12 12"><circle cx="6" cy="6" r="5" fill="none" stroke="var(--ink)" stroke-width="1.2"/><path d="M3.5,6 L5.4,7.8 L8.6,4.4" fill="none" stroke="var(--ink)" stroke-width="1.2"/></svg>People Living with Spinal Injuries</li>
    <li class="class-item"><svg width="12" height="12" viewBox="0 0 12 12"><circle cx="6" cy="6" r="5" fill="none" stroke="var(--ink)" stroke-width="1.2"/><path d="M3.5,6 L5.4,7.8 L8.6,4.4" fill="none" stroke="var(--ink)" stroke-width="1.2"/></svg>Schools</li>
    <li class="class-item"><svg width="12" height="12" viewBox="0 0 12 12"><circle cx="6" cy="6" r="5" fill="none" stroke="var(--ink)" stroke-width="1.2"/><path d="M3.5,6 L5.4,7.8 L8.6,4.4" fill="none" stroke="var(--ink)" stroke-width="1.2"/></svg>Amateur Under 18 Photographers</li>
    <li class="class-item"><svg width="12" height="12" viewBox="0 0 12 12"><circle cx="6" cy="6" r="5" fill="none" stroke="var(--ink)" stroke-width="1.2"/><path d="M3.5,6 L5.4,7.8 L8.6,4.4" fill="none" stroke="var(--ink)" stroke-width="1.2"/></svg>Amateur Over 18 Photographers</li>
    <li class="class-item"><svg width="12" height="12" viewBox="0 0 12 12"><circle cx="6" cy="6" r="5" fill="none" stroke="var(--ink)" stroke-width="1.2"/><path d="M3.5,6 L5.4,7.8 L8.6,4.4" fill="none" stroke="var(--ink)" stroke-width="1.2"/></svg>Charities</li>
    <li class="class-item"><svg width="12" height="12" viewBox="0 0 12 12"><circle cx="6" cy="6" r="5" fill="none" stroke="var(--ink)" stroke-width="1.2"/><path d="M3.5,6 L5.4,7.8 L8.6,4.4" fill="none" stroke="var(--ink)" stroke-width="1.2"/></svg>Professional Photographers</li>
  </ul>

  <div class="contact">
    <span><svg width="22" height="22" viewBox="0 0 22 22"><circle cx="11" cy="11" r="10" fill="none" stroke="var(--white)" stroke-width="2"/><path d="M8,6 C6,8 8,13 10,15 C12,17 15,17 16,15 L14,13 L12.5,14 C11,13 9,11 8.5,9.5 L9.5,8 Z" fill="var(--white)"/></svg>+44 (0)1632 960418</span>
    <span><svg width="22" height="22" viewBox="0 0 22 22"><circle cx="11" cy="11" r="10" fill="none" stroke="var(--white)" stroke-width="2"/><ellipse cx="11" cy="11" rx="4" ry="10" fill="none" stroke="var(--white)" stroke-width="1.5"/><line x1="1" y1="11" x2="21" y2="11" stroke="var(--white)" stroke-width="1.5"/></svg>www.hmfcharity-example.org.uk</span>
  </div>
  <div class="social one" aria-label="Social page"></div>
  <div class="social two" aria-label="Social page"></div>

  <p class="legal">Registered charity No. 1098452 Please note that this is an initial "draft" and any published "flyer / web page will have to meet current UK Charity Regulations.</p>
</main>
</body>
</html>
```